New Branding Concept Healthcare Course Brochure

OBJECTIVE:
We need a new course brochure design to meet match our new branding colour scheme & concept as we are currently in the process of upgrading our website design. This A4 double sided brochure will briefly showcase a course on offer, in a clear, concise, professional and engaging way. This brochure will be in line with our new branding colour scheme and concept.
Our concept in monochrome with spashes & pops of colour (matching our logo colours) - see examples attached of imagery being used for social media currently as this somewhat reflects the concept we are working towards after, in terms of colour and look.

We are happy for you to be creative with formats. However, it must be able to include the same information as attached in "disability course brochure information". Have also attached some 'format examples' that we like - this is purely for ideas of paragraphing and formatting of information that other training providers are using, not for colour and graphic examples.

The final design will be used for promotional and adverting purposes to communicate information about a course to a prospective student in both print and soft copy form.

ORGANISATION OVERVIEW:
Brightward Learning (RTO.47318)
03 9417 2856
www.brightwardlearning.edu.au
admin@bwl.edu.au
Head Office (Admin only): Level 4, 57 Corlette Street, Blackburn VIC 3130
3 modern & fully equipped training campuses across Melbourne: Blackburn (Tallowood Road), Preston & Narre Warren.
We are a private registered training organisation based in Melbourne, Victoria, Australia specialising in only healthcare courses such as certificate III in pathology collection, Certificate IV in Disability, Certificate III in individual Support, Certificate IV in Aged Care & Certificate III in Health Services Assistance. We also offer professional development training workshops to corporate clients and the public such as first aid, cpr, medications, food saftey, manual handling and much more.

Target Market(s)

Prospective Healthcare Education Students

Font styles to use
Serif

Colors
f37122
fbed22
ffffff

Requirements
Must have
• MUST INCLUDE:
- QVS Logo (attached)
- Our Logo (attached)
- Our slogan (Making you the future of healthcare)
- QR Code
- pops of colour must match our logo colours (see guide attached)
- contact details: website, social media buttons (instagram, facebook & twitter), phone number, email & our head office address.
- Must include relevant imagery (in this case disability or disability carer related, steer away from wheelchair images as it's used too much)
- must include information items (as per attached "disability brochure course information"

```html
<!DOCTYPE html>
<html lang="en">
<head>
<meta charset="utf-8">
<title>Brightward Learning – Certificate IV in Disability brochure</title>
<link href="https://fonts.googleapis.com/css2?family=Fira+Sans:wght@300;400;500;700;900&display=swap" rel="stylesheet">
<style>
:root{
  --orange:#e8501c;
  --yellow:#fdd000;
  --ink:#1a1a1a;
  --text:#333333;
  --grey:#595959;
  --rule:#6b6b6b;
  --backdrop:#cdcdcd;
  --white:#ffffff;
  --photo-warm-a:#8a7a70;
  --photo-warm-b:#d9d2cb;
  --photo-green-a:#5f8d3a;
  --photo-green-b:#b9d48f;
}
*{box-sizing:border-box;margin:0;padding:0}
html,body{width:1200px;height:1200px;overflow:hidden;background:var(--backdrop)}
body{position:relative;font-family:"Fira Sans",Arial,sans-serif;color:var(--text)}
.page{position:absolute;top:207px;width:872px;height:1263px;background:var(--white);overflow:hidden;transform:scale(.6211);transform-origin:0 0}
.page--front{left:56px}
.page--back{left:620px}
.abs{position:absolute}
.brand{position:absolute;display:flex;align-items:center;gap:14px}
.brand__dot{width:62px;height:62px;border-radius:50%;background:var(--orange)}
.brand__name{font-size:31px;font-weight:500;color:var(--grey);line-height:1.05;letter-spacing:.5px}
.brand__id{font-size:8px;color:var(--grey);margin-top:6px;letter-spacing:.5px}
.heading{font-size:18px;font-weight:300;color:var(--ink);text-transform:uppercase;padding-bottom:8px;border-bottom:1px solid var(--rule);margin-bottom:10px;letter-spacing:.2px}
.heading b{font-weight:700;color:var(--orange)}
.heading--dark b{color:var(--ink)}
.body{font-size:12.6px;font-weight:300;line-height:16.4px;color:var(--text)}
.body p{margin-bottom:8px}
.body strong{font-weight:700;color:var(--ink)}
.hl{color:var(--orange);font-weight:500}
.bullets{list-style:none;margin:10px 0 10px 26px}
.bullets li{position:relative;padding-left:13px;margin-bottom:5px}
.bullets li::before{content:"";position:absolute;left:0;top:5px;width:8px;height:8px;border-radius:50%;background:var(--orange)}
.hero-band{position:absolute;left:0;top:160px;width:520px;height:168px;background:var(--yellow)}
.slogan{position:absolute;left:34px;top:170px;font-size:44px;font-weight:900;line-height:41px;color:var(--ink);letter-spacing:-.3px}
.tagline{position:absolute;left:36px;top:298px;font-size:17px;font-weight:300;color:var(--ink)}
.course-title{position:absolute;left:34px;top:350px;font-size:17px;font-weight:700;color:var(--orange)}
.divider{position:absolute;left:434px;top:437px;width:1px;height:697px;background:var(--rule)}
.apply{position:absolute;left:0;width:100%;top:1170px;display:flex;justify-content:center;align-items:center;gap:10px;font-size:14.5px;font-weight:300;color:var(--ink)}
.apply__label{font-size:17px;font-weight:700;color:var(--orange)}
.apply__link{font-weight:700;color:var(--orange);display:flex;align-items:center;gap:6px}
.footer{position:absolute;left:0;bottom:0;width:100%;height:63px;background:var(--yellow);display:flex;justify-content:space-around;align-items:flex-start;padding:10px 28px 0;font-size:12.6px;font-weight:500;color:var(--ink)}
.footer span{display:flex;align-items:center;gap:5px}
.icon{width:17px;height:17px;flex:none}
.badge{position:absolute;left:700px;top:1078px;width:90px;height:78px;background:#c8d6cf;border-radius:3px}
.units{border-collapse:collapse;width:434px;font-size:12.4px;font-weight:300;color:var(--ink)}
.units td,.units th{border:1px solid var(--rule);padding:3px 8px;line-height:15.5px;height:26px;text-align:left}
.units .cap{text-align:center;font-weight:500;font-size:13.5px;height:25px}
.units .colhead{font-weight:500;font-size:12.4px;height:22px}
.units td.code{width:90px;color:var(--orange);font-weight:400;padding-left:6px}
.note{font-size:8.4px;font-weight:300;line-height:11px;color:var(--ink)}
.questions{position:absolute;left:494px;top:930px;width:378px;height:227px;background:var(--orange);color:var(--white);padding:10px 10px 0 10px}
.questions h3{font-size:18px;font-weight:700;margin-bottom:6px}
.questions p{font-size:12.6px;font-weight:300;line-height:16.4px;color:#ffe3d6}
.q-row{display:flex;gap:16px;align-items:center;font-size:12.6px;font-weight:500;margin-top:14px}
.q-row span{display:flex;gap:6px;align-items:center}
.socials{display:flex;gap:6px;justify-content:center;margin-top:12px}
.socials i{width:18px;height:18px;border-radius:50%;background:var(--white);display:block}
</style>
</head>
<body>

<!-- Front page -->
<section class="page page--front">
  <div class="brand" style="left:34px;top:62px">
    <div class="brand__dot"></div>
    <div>
      <div class="brand__name">brightward<br>learning</div>
      <div class="brand__id">TOID 47318</div>
    </div>
  </div>

  <div class="hero-band"></div>
  <svg class="abs" style="left:0;top:0" width="872" height="600" viewBox="0 0 872 600">
    <circle cx="680" cy="222" r="252" fill="var(--orange)"/>
    <defs>
      <linearGradient id="portrait" x1="0" y1="0" x2="1" y2="1">
        <stop offset="0" stop-color="var(--photo-warm-a)"/>
        <stop offset="1" stop-color="var(--photo-warm-b)"/>
      </linearGradient>
    </defs>
    <circle cx="683" cy="222" r="222" fill="url(#portrait)" role="img" aria-label="Photo: smiling older woman seated in a chair while a carer rests hands on her shoulder"/>
  </svg>
  <h1 class="slogan">Making you<br>the future of<br>healthcare</h1>
  <div class="tagline">apply today!</div>
  <div class="course-title">CHC43115 Certificate IV in Disability</div>

  <div class="divider"></div>

  <div class="abs body" style="left:34px;top:408px;width:366px">
    <h2 class="heading"><b>Course</b> Overview</h2>
    <p>Start your rewarding career in disability with Brightward Learning and become a job-ready disability support worker (DSW).</p>
    <p style="margin-top:12px">This qualification reflects the role of workers in a range of community settings and clients’ homes, who provide training and support in a manner that empowers people with disabilities to achieve greater levels of independence, self-reliance, community participation and wellbeing, workers promote a person-centred approach and more.</p>
    <p>Brightward Learning is committed to providing an inclusive learning environment. Principles of access and equity for all students are applied in all programs. People with disabilities are encouraged to apply</p>

    <h2 class="heading" style="margin-top:18px"><b>Job</b> Prospects</h2>
    <p>Possible outcomes may include:</p>
    <ul class="bullets">
      <li>Community Worker</li>
      <li>Disabilities Services Officer</li>
      <li>Disability Support Worker</li>
    </ul>
    <p style="margin-top:14px"><span class="hl">Delivery Locations:</span> Blackburn, Narre Warren &amp; Preston</p>
    <p style="margin-top:12px"><span class="hl">Duration:</span></p>
    <ul class="bullets" style="margin-top:6px">
      <li>22 weeks* of 1 day per week (9am-4.30pm) or;</li>
      <li>30 weeks* of 1 evening per week (5pm-9pm)<br>+ 3 Saturdays (9am-4.30pm)</li>
    </ul>
    <p style="margin-top:18px">Delivery location &amp; duration varies between intakes. Please refer to our website at <span class="hl">www.brightwardlearning.edu.au</span> for upcoming course availability</p>
    <p><span class="hl">Delivery Mode:</span> <span style="font-weight:400">Classroom &amp; blended/virtual learning</span></p>

    <h2 class="heading heading--dark" style="margin-top:22px"><b>Practical Experience</b> and Assessment:</h2>
    <p style="margin-top:14px">Is undertaken throughout the course in the Brightward Learning simulated environment with trainers who are experts in their field and maintain currency in the industry.</p>
  </div>

  <div class="abs body" style="left:469px;top:556px;width:372px">
    <h2 class="heading"><b>Course Entry</b> Requirements</h2>
    <p>This is an open entry program of study with participants needing to read, write and communicate in English to a level to perform the job. For further detailed information regarding entry requirements, please visit: www.brightwardlearning.edu.au/certificate-4-in-disability</p>

    <h2 class="heading" style="margin-top:18px"><b>Govt. Subsidised</b> Training</h2>
    <p style="margin-top:14px">This training is delivered with Victorian and Commonwealth Government funding under the Skills Forward Program and may impact your access to further government subsidised training.</p>
    <p style="margin-top:12px">To find out if you are eligible, please <strong>contact us on 03 9417 2856</strong> to discuss your circumstances or visit: <strong>www.brightwardlearning.edu.au/funded-courses.html</strong></p>

    <h2 class="heading" style="margin-top:26px"><b>Tuition</b> Fees</h2>
    <p style="margin-top:14px">The student tuition fees as published are subject to change given individual circumstances at enrolment.</p>
    <p style="margin-top:10px">Full Fee: <span class="hl">$3,200</span><br>Government Funded: <span class="hl">$250</span><br>Government Funded With Health Care Card, Pensioner Concession Card or Vet Gold Card: <span class="hl">$250</span></p>
    <p>For detailed information regarding our course fees &amp; payment plans available please visit: <strong>www.brightwardlearning.edu.au/certificate-4-in-disability</strong></p>
  </div>
  <div class="badge" role="img" aria-label="QVS accreditation badge"></div>

  <div class="apply">
    <span class="apply__label">How to Apply</span>
    <span>Complete an ‘online application form’ by clicking the below link</span>
    <span class="apply__link"><svg class="icon" viewBox="0 0 20 20"><circle cx="10" cy="10" r="8" fill="none" stroke="currentColor" stroke-width="1.5"/><path d="M2 10h16M10 2c-4 4-4 12 0 16M10 2c4 4 4 12 0 16" fill="none" stroke="currentColor" stroke-width="1.2"/></svg>www.brightwardlearning.edu.au/apply</span>
  </div>
  <div class="footer">
    <span><svg class="icon" viewBox="0 0 20 20"><path d="M5 2l3 4-2 2c1 3 3 5 6 6l2-2 4 3-2 3C8 17 3 12 2 4z" fill="none" stroke="currentColor" stroke-width="1.5"/></svg>03 9417 2856</span>
    <span><svg class="icon" viewBox="0 0 20 20"><rect x="2" y="5" width="16" height="11" fill="none" stroke="currentColor" stroke-width="1.5"/><path d="M2 5l8 6 8-6" fill="none" stroke="currentColor" stroke-width="1.5"/></svg>admin@bwl.edu.au</span>
    <span><svg class="icon" viewBox="0 0 20 20"><circle cx="10" cy="10" r="8" fill="none" stroke="currentColor" stroke-width="1.5"/><path d="M2 10h16M10 2c-4 4-4 12 0 16M10 2c4 4 4 12 0 16" fill="none" stroke="currentColor" stroke-width="1.2"/></svg>www.brightwardlearning.edu.au</span>
    <span><svg class="icon" viewBox="0 0 20 20"><path d="M10 18s-6-6-6-10a6 6 0 0112 0c0 4-6 10-6 10z" fill="none" stroke="currentColor" stroke-width="1.5"/><circle cx="10" cy="8" r="2" fill="currentColor"/></svg>Level 4, 57 Corlette Street, Blackburn VIC 3130</span>
  </div>
</section>

<!-- Back page -->
<section class="page page--back">
  <svg class="abs" style="left:0;top:0" width="872" height="350" viewBox="0 0 872 350">
    <defs>
      <linearGradient id="garden" x1="0" y1="0" x2="1" y2="1">
        <stop offset="0" stop-color="var(--photo-green-a)"/>
        <stop offset="1" stop-color="var(--photo-green-b)"/>
      </linearGradient>
    </defs>
    <polygon points="0,0 872,0 872,200 690,345 0,95" fill="url(#garden)" role="img" aria-label="Photo: young carer and older woman in a wheelchair enjoying a green park"/>
    <polygon points="0,95 600,313 0,140" fill="var(--orange)"/>
  </svg>

  <div class="brand" style="left:34px;top:252px">
    <div class="brand__dot"></div>
    <div>
      <div class="brand__name">brightward<br>learning</div>
      <div class="brand__id">TOID 47318</div>
    </div>
  </div>

  <div class="abs body" style="left:34px;top:366px;width:362px">
    <h2 class="heading"><b>Practical</b> Placement</h2>
    <p>Practical placement of 120 hours is a mandatory requirement of this course. Brightward Learning will organise on our students behalf.</p>
    <h2 class="heading" style="margin-top:16px"><b>Units of</b> Competency</h2>
    <p>16 units of competency are required to successfully complete this qualification. This incudes 11 core units and 5 elective units, along with 120 hours of practical work placement.</p>
  </div>

  <div class="abs" style="left:33px;top:562px">
    <table class="units">
      <tr><th class="cap" colspan="2">Core Units</th></tr>
      <tr><th class="colhead">Unit Code</th><th class="colhead">Units of Competency</th></tr>
      <tr><td class="code">CHCCCS015</td><td>Provide individualised Support</td></tr>
      <tr><td class="code">CHCDIS002</td><td>Follow established person centred behaviour supports</td></tr>
      <tr><td class="code">CHCDIS005</td><td>Develop and provide person centred service responses</td></tr>
      <tr><td class="code">CHCDIS007</td><td>Facilitate the empowerment of people with disability</td></tr>
      <tr><td class="code">CHCDIS008</td><td>Facilitate community participation and social inclusion</td></tr>
      <tr><td class="code">CHCDIS009</td><td>Facilitate ongoing skills development using a person centred approach</td></tr>
      <tr><td class="code">CHCDIS010</td><td>Provide person centred services to people with disability with complex needs</td></tr>
      <tr><td class="code">CHCDIV001</td><td>Work with diverse people</td></tr>
      <tr><td class="code">CHCLEG003</td><td>Manage legal and ethical compliance</td></tr>
      <tr><td class="code">HLTAAP001</td><td>Recognise healthy body systems</td></tr>
      <tr><td class="code">HLTWHS002</td><td>Follow safe work practices for direct client care</td></tr>
    </table>
    <table class="units" style="margin-top:14px">
      <tr><th class="cap" colspan="2">Elective units</th></tr>
      <tr><td class="code">HLTFSE001</td><td>Follow basic food safety practices</td></tr>
      <tr><td class="code">CHCCCS011</td><td>Meet personal support needs</td></tr>
      <tr><td class="code">CHCLAH001</td><td>Work effectively with in the leisure and health industries</td></tr>
      <tr><td class="code">HLTAID003</td><td>Provide first aid</td></tr>
      <tr><td class="code">HLTINF001</td><td>Comply with infection prevention and control policies and procedures</td></tr>
    </table>
    <p class="note" style="margin-top:6px;width:445px">Competency is assessed through a combination of practical application and demonstration of skills, research, analysis and completion of competency based workbooks.</p>
  </div>

  <div class="abs body" style="left:500px;top:380px;width:338px">
    <h2 class="heading" style="line-height:22px"><b>Opportunity for</b><br>Credit Transfe rs (CT)</h2>
    <p style="margin-top:14px">If students have already successfully completed unit/s of competency which are included within the qualification Brightward Learning offers, credit may be granted.</p>
    <h2 class="heading" style="line-height:22px;margin-top:38px"><b>Opportunity for Recognition</b><br>of Prior Learning (RPL)</h2>
    <p style="margin-top:12px">Competencies gained through other formal study or experience may be acknowledged through a recognition process.</p>
    <h2 class="heading" style="margin-top:14px"><b>Pathways</b></h2>
    <p style="margin-top:14px">A possible training pathway for a participant completing this qualification could be any specialised area in the health sector or courses similar to the following: Certificate IV in Community Services; Certificate IV in Leisure and Health; Certificate IV in Ageing Support; Diploma of Community Services; Diploma of Nursing; Diploma of Leisure and Health</p>
    <h2 class="heading" style="margin-top:6px"><b>Next Course</b> Commencing</h2>
    <p style="margin-top:14px">Regular intakes are available throughout the year. Please refer to our website at www.brightwardlearning.edu.au for upcoming course dates.</p>
  </div>

  <div class="questions">
    <h3>QUESTIONS?</h3>
    <p>Should you have any questions regarding Brightward Learning and the course, please contact one of our friendly team members on:</p>
    <div class="q-row">
      <span><svg class="icon" viewBox="0 0 20 20"><path d="M5 2l3 4-2 2c1 3 3 5 6 6l2-2 4 3-2 3C8 17 3 12 2 4z" fill="none" stroke="currentColor" stroke-width="1.5"/></svg>03 9417 2856</span>
      <span><svg class="icon" viewBox="0 0 20 20"><rect x="2" y="5" width="16" height="11" fill="none" stroke="currentColor" stroke-width="1.5"/><path d="M2 5l8 6 8-6" fill="none" stroke="currentColor" stroke-width="1.5"/></svg>admin@bwl.edu.au</span>
    </div>
    <div class="q-row" style="margin-top:10px">
      <span><svg class="icon" viewBox="0 0 20 20"><circle cx="10" cy="10" r="8" fill="none" stroke="currentColor" stroke-width="1.5"/><path d="M2 10h16M10 2c-4 4-4 12 0 16M10 2c4 4 4 12 0 16" fill="none" stroke="currentColor" stroke-width="1.2"/></svg>www.brightwardlearning.edu.au</span>
    </div>
    <div class="q-row" style="margin-top:10px;align-items:flex-start">
      <span style="align-items:flex-start"><svg class="icon" viewBox="0 0 20 20"><path d="M10 18s-6-6-6-10a6 6 0 0112 0c0 4-6 10-6 10z" fill="none" stroke="currentColor" stroke-width="1.5"/><circle cx="10" cy="8" r="2" fill="currentColor"/></svg>Head Office<br>Level 4, 57 Corlette Street, Blackburn VIC 3130</span>
    </div>
    <div class="socials"><i></i><i></i><i></i><i></i><i></i><i></i></div>
  </div>

  <div class="apply" style="top:1173px">
    <span class="apply__label">How to Apply</span>
    <span>Complete an ‘online application form’ by clicking the below link</span>
    <span class="apply__link"><svg class="icon" viewBox="0 0 20 20"><circle cx="10" cy="10" r="8" fill="none" stroke="currentColor" stroke-width="1.5"/><path d="M2 10h16M10 2c-4 4-4 12 0 16M10 2c4 4 4 12 0 16" fill="none" stroke="currentColor" stroke-width="1.2"/></svg>www.brightwardlearning.edu.au/apply</span>
  </div>
  <div class="footer">
    <span><svg class="icon" viewBox="0 0 20 20"><path d="M5 2l3 4-2 2c1 3 3 5 6 6l2-2 4 3-2 3C8 17 3 12 2 4z" fill="none" stroke="currentColor" stroke-width="1.5"/></svg>03 9417 2856</span>
    <span><svg class="icon" viewBox="0 0 20 20"><rect x="2" y="5" width="16" height="11" fill="none" stroke="currentColor" stroke-width="1.5"/><path d="M2 5l8 6 8-6" fill="none" stroke="currentColor" stroke-width="1.5"/></svg>admin@bwl.edu.au</span>
    <span><svg class="icon" viewBox="0 0 20 20"><circle cx="10" cy="10" r="8" fill="none" stroke="currentColor" stroke-width="1.5"/><path d="M2 10h16M10 2c-4 4-4 12 0 16M10 2c4 4 4 12 0 16" fill="none" stroke="currentColor" stroke-width="1.2"/></svg>www.brightwardlearning.edu.au</span>
    <span><svg class="icon" viewBox="0 0 20 20"><path d="M10 18s-6-6-6-10a6 6 0 0112 0c0 4-6 10-6 10z" fill="none" stroke="currentColor" stroke-width="1.5"/><circle cx="10" cy="8" r="2" fill="currentColor"/></svg>Level 4, 57 Corlette Street, Blackburn VIC 3130</span>
  </div>
</section>

</body>
</html>
```